Full re-design of visual identity

We have just re-designed our logo and would like to apply it on our folders, business cards, stationery, and etc... we are attaching new logo + the material we need to re-design... we will provide full corel draw files to help make job easier and also because lot of icons and artwork can be still used...

any doubts we are at your disposal. thanks in advance.

```html
<!DOCTYPE html>
<html lang="en">
<head>
<meta charset="utf-8">
<title>Novalink – DL Envelope Stationery</title>
<link rel="stylesheet" href="https://fonts.googleapis.com/css2?family=Poppins:wght@400;600&display=swap">
<style>
  :root {
    --canvas-bg: #f2f2f2;
    --envelope-dark: #4b4b4b;
    --envelope-mid: #666666;
    --envelope-white: #ffffff;
    --brand-orange: #e8792a;
    --logo-grey: #8c8c8c;
    --contact-text: #e6e6e6;
    --fold-line: #3e3e3e;
  }
  * { margin: 0; padding: 0; box-sizing: border-box; }
  html, body {
    width: 1200px; height: 1000px; overflow: hidden;
    background: var(--canvas-bg);
    font-family: "Poppins", sans-serif;
  }
  .sheet {
    position: relative; width: 1200px; height: 1000px;
  }
  .envelope {
    position: absolute; left: 200px;
    width: 800px; height: 400px;
    overflow: hidden;
    background: linear-gradient(135deg, var(--envelope-dark) 0%, var(--envelope-mid) 60%, var(--envelope-dark) 100%);
    box-shadow: 0 10px 28px rgba(0,0,0,0.14);
  }
  .envelope--back { top: 70px; }
  .envelope--front { top: 530px; }

  .envelope__art { position: absolute; inset: 0; }

  .brand {
    position: absolute; display: flex; align-items: center; gap: 8px;
    font-weight: 600; color: var(--logo-grey); letter-spacing: -0.5px;
  }
  .brand__mark { background: var(--brand-orange); }
  .brand--back { right: 44px; top: 116px; font-size: 30px; }
  .brand--back .brand__mark { width: 14px; height: 14px; }
  .brand--front { left: 86px; top: 170px; font-size: 52px; }
  .brand--front .brand__mark { width: 22px; height: 22px; }

  .contact-list {
    position: absolute; left: 44px; bottom: 40px;
    list-style: none; color: var(--contact-text);
    font-size: 11.5px; line-height: 1.45;
  }
  .contact-list li { display: flex; align-items: flex-start; gap: 10px; margin-bottom: 4px; }
  .contact-list svg { flex: 0 0 12px; margin-top: 2px; }

  .address-window {
    position: absolute; right: 60px; top: 130px;
    width: 300px; height: 140px;
    background: var(--envelope-white);
    border-radius: 8px;
  }
</style>
</head>
<body>
<main class="sheet">

  <section class="envelope envelope--back" aria-label="Envelope back">
    <svg class="envelope__art" width="800" height="400" viewBox="0 0 800 400">
      <path d="M800 0 L800 400 L330 400 C520 330 690 200 740 0 Z" fill="var(--envelope-white)"/>
      <line x1="0" y1="52" x2="748" y2="52" stroke="var(--fold-line)" stroke-width="1.5" opacity="0.6"/>
    </svg>
    <div class="brand brand--back"><span class="brand__name">Novalink</span><span class="brand__mark"></span></div>
    <ul class="contact-list">
      <li>
        <svg width="12" height="12" viewBox="0 0 12 12"><path d="M6 0.5a4 4 0 0 0-4 4c0 3 4 7 4 7s4-4 4-7a4 4 0 0 0-4-4zm0 5.5a1.5 1.5 0 1 1 0-3 1.5 1.5 0 0 1 0 3z" fill="var(--brand-orange)"/></svg>
        <span>123, Main Street, Anytown,<br>Postal Code, Country</span>
      </li>
      <li>
        <svg width="12" height="12" viewBox="0 0 12 12"><path d="M2.5 1l2 2-1 1.5c.8 1.6 2 2.8 3.5 3.5l1.5-1 2 2-1.5 2C4.5 10.5 1.5 7.5 .5 2.5z" fill="var(--brand-orange)"/></svg>
        <span>555-1234-56</span>
      </li>
      <li>
        <svg width="12" height="12" viewBox="0 0 12 12"><rect x="1" y="3" width="10" height="7" rx="1" fill="var(--brand-orange)"/><rect x="3" y="1" width="6" height="3" fill="var(--brand-orange)"/></svg>
        <span>555-1234-56</span>
      </li>
      <li>
        <svg width="12" height="12" viewBox="0 0 12 12"><rect x="0.5" y="2.5" width="11" height="7.5" rx="1" fill="var(--brand-orange)"/><path d="M1 3l5 4 5-4" stroke="var(--envelope-dark)" stroke-width="1" fill="none"/></svg>
        <span>we@youraddress.com</span>
      </li>
      <li>
        <svg width="12" height="12" viewBox="0 0 12 12"><circle cx="6" cy="6" r="5" fill="none" stroke="var(--brand-orange)" stroke-width="1.4"/><path d="M1 6h10M6 1c2 2.5 2 7.5 0 10M6 1c-2 2.5-2 7.5 0 10" stroke="var(--brand-orange)" stroke-width="1" fill="none"/></svg>
        <span>www.yourwebsite.com</span>
      </li>
    </ul>
  </section>

  <section class="envelope envelope--front" aria-label="Envelope front">
    <div class="brand brand--front"><span class="brand__name">Novalink</span><span class="brand__mark"></span></div>
    <div class="address-window" aria-label="Address window"></div>
  </section>

</main>
</body>
</html>
```